10-year customer thank you card

We want a greeting card that our sales reps can send to companies/customers who have been with our company for 10 or more years. We're a software company, our corporate color is blue but we also like green, orange, and purple. We'd like something rather minimal/simplistic for this card, perhaps building off our tree logo. We're really open to ideas for this one. You must use the template files that are uploaded. Copy included in 10 year thank you card file; the copy may change based on how it looks when laid out
Updates

I updated our brief. We'd prefer a sans serif font. I also uploaded a blank infographic image that includes more of our approved colors.

Industry/Entity Type

Software

Font styles to use
Sans Serif

```html
<!DOCTYPE html>
<html lang="en">
<head>
<meta charset="utf-8">
<title>Ten Years – Thank You Cards</title>
<link href="https://fonts.googleapis.com/css2?family=Lato:wght@400&display=swap" rel="stylesheet">
<style>
  :root {
    --brand-blue: #1a80c3;
    --brand-green: #a9cf46;
    --brand-orange: #f48a34;
    --brand-purple: #543e8d;
    --paper: #ffffff;
    --trim: #c8c8c8;
  }
  * { margin: 0; padding: 0; box-sizing: border-box; }
  html, body { width: 858px; height: 1200px; overflow: hidden; background: var(--paper); }
  .sheet { position: relative; width: 858px; height: 1200px; font-family: "Lato", "Helvetica Neue", Arial, sans-serif; color: var(--brand-blue); }

  .card { position: absolute; left: 0; width: 858px; height: 600px; }
  .card--top { top: 0; }
  .card--bottom { top: 598px; height: 601px; border: 1px solid var(--trim); }

  .headline, .closing { position: absolute; width: 100%; text-align: center; line-height: 1; font-weight: 400; white-space: nowrap; }
  .headline { left: -13px; font-size: 68px; }
  .closing { left: -29px; font-size: 54px; }
  .card--top .headline { top: 180px; }
  .card--top .closing { top: 462px; }
  .card--bottom .headline { top: 219px; }
  .card--bottom .closing { top: 498px; }

  .tree-row, .gift-row { position: absolute; left: 0; width: 100%; height: 0; }
  .tree { position: absolute; border-radius: 4px 4px 2px 2px; }
  .card--top .tree-row { top: 320px; }
  .card--top .tree { width: 58px; height: 80px; }
  .card--bottom .tree-row { top: 326px; }
  .card--bottom .tree { width: 43px; height: 63px; }
  .gift-row { top: 393px; }
  .gift { position: absolute; width: 43px; height: 81px; }

  .blue { background: var(--brand-blue); }
  .green { background: var(--brand-green); }
  .orange { background: var(--brand-orange); }
  .purple { background: var(--brand-purple); }
</style>
</head>
<body>
<main class="sheet">

  <section class="card card--top">
    <h1 class="headline">Ten Years</h1>
    <div class="tree-row">
      <div class="tree blue" style="left:26px" role="img" aria-label="Scribbled blue tree"></div>
      <div class="tree green" style="left:106px" role="img" aria-label="Scribbled green tree"></div>
      <div class="tree orange" style="left:188px" role="img" aria-label="Scribbled orange tree"></div>
      <div class="tree purple" style="left:268px" role="img" aria-label="Scribbled purple tree"></div>
      <div class="tree blue" style="left:348px" role="img" aria-label="Scribbled blue tree"></div>
      <div class="tree green" style="left:429px" role="img" aria-label="Scribbled green tree"></div>
      <div class="tree orange" style="left:509px" role="img" aria-label="Scribbled orange tree"></div>
      <div class="tree purple" style="left:590px" role="img" aria-label="Scribbled purple tree"></div>
      <div class="tree blue" style="left:670px" role="img" aria-label="Scribbled blue tree"></div>
      <div class="tree green" style="left:751px" role="img" aria-label="Scribbled green tree"></div>
    </div>
    <p class="closing">Thank you!</p>
  </section>

  <section class="card card--bottom">
    <h1 class="headline">Ten Years</h1>
    <div class="tree-row">
      <div class="tree blue" style="left:21px" role="img" aria-label="Scribbled blue tree"></div>
      <div class="tree green" style="left:107px" role="img" aria-label="Scribbled green tree"></div>
      <div class="tree orange" style="left:193px" role="img" aria-label="Scribbled orange tree"></div>
      <div class="tree purple" style="left:279px" role="img" aria-label="Scribbled purple tree"></div>
      <div class="tree blue" style="left:364px" role="img" aria-label="Scribbled blue tree"></div>
      <div class="tree green" style="left:450px" role="img" aria-label="Scribbled green tree"></div>
      <div class="tree orange" style="left:535px" role="img" aria-label="Scribbled orange tree"></div>
      <div class="tree purple" style="left:621px" role="img" aria-label="Scribbled purple tree"></div>
      <div class="tree blue" style="left:706px" role="img" aria-label="Scribbled blue tree"></div>
      <div class="tree green" style="left:792px" role="img" aria-label="Scribbled green tree"></div>
    </div>
    <div class="gift-row">
      <div class="gift blue" style="left:21px"></div>
      <div class="gift green" style="left:107px"></div>
      <div class="gift orange" style="left:193px"></div>
      <div class="gift purple" style="left:279px"></div>
      <div class="gift blue" style="left:364px"></div>
      <div class="gift green" style="left:450px"></div>
      <div class="gift orange" style="left:535px"></div>
      <div class="gift purple" style="left:621px"></div>
      <div class="gift blue" style="left:706px"></div>
      <div class="gift green" style="left:792px"></div>
    </div>
    <p class="closing">Thank you!</p>
  </section>

</main>
</body>
</html>
```